Card design for orthopaedic surgeons working as The Brightwater Joint Centre

Business cards, letterhead

Colors

Designer to choose colors to be used in the design.

Requirements
Must have
• Late addition.
• Cards letterhead must have logos of
• Crestmoor Lindell College of Surgeons
• Varenwood Bone Health Association
Nice to have
• Back of card to have space for appointment time to be added by hand and some blank space for writing incidental other notes.

```html
<!DOCTYPE html>
<html lang="en">
<head>
<meta charset="utf-8">
<title>The Brightwater Joint Centre – Business Card</title>
<link rel="stylesheet" href="https://fonts.googleapis.com/css2?family=Open+Sans:wght@400;600&family=Arimo:wght@700&display=swap">
<style>
  :root {
    --sky: #33b3ff;
    --sky-soft: #5cc3ff;
    --navy: #0b3550;
    --ink: #1f1f1f;
    --paper: #ffffff;
    --backdrop-top: #b3b3b3;
    --backdrop-bottom: #e4e4e4;
  }
  * { box-sizing: border-box; margin: 0; padding: 0; }
  html, body { width: 1200px; height: 1200px; overflow: hidden; }
  body {
    background: linear-gradient(180deg, var(--backdrop-top), var(--backdrop-bottom));
    font-family: "Open Sans", Arial, sans-serif;
    color: var(--ink);
    position: relative;
  }
  .card {
    position: absolute;
    left: 250px;
    width: 700px;
    height: 400px;
    background: var(--paper);
    border-radius: 42px;
    overflow: hidden;
    box-shadow: 0 10px 24px rgba(0,0,0,0.18);
  }
  .card--back { top: 150px; }
  .card--front { top: 640px; }

  .wordmark {
    font-family: "Open Sans", Arial, sans-serif;
    font-weight: 400;
    color: var(--sky);
    letter-spacing: -0.5px;
    white-space: nowrap;
  }
  .card--back .wordmark {
    position: absolute;
    top: 135px;
    left: 0; right: 0;
    text-align: center;
    font-size: 40px;
  }
  .card--back .web-address {
    position: absolute;
    top: 215px;
    left: 0; right: 0;
    text-align: center;
    font-size: 21px;
    letter-spacing: 6px;
    color: var(--ink);
  }

  .card--front .wordmark {
    position: absolute;
    top: 34px;
    left: 120px;
    font-size: 34px;
  }
  .card-band {
    position: absolute;
    left: 0; right: 0; bottom: 0;
    height: 72px;
    background: linear-gradient(180deg, var(--sky-soft), var(--sky));
  }
  .holder {
    position: absolute;
    top: 106px;
    left: 96px;
  }
  .holder-name {
    font-family: "Arimo", Arial, sans-serif;
    font-weight: 700;
    font-size: 27px;
    color: var(--navy);
  }
  .holder-title {
    font-family: "Open Sans", Arial, sans-serif;
    font-weight: 400;
    font-size: 22px;
    color: var(--sky);
  }
  .holder-address {
    margin-top: 10px;
    font-size: 18px;
    line-height: 23px;
  }
  .contact-list { list-style: none; margin-top: 14px; }
  .contact-list li {
    display: flex;
    align-items: center;
    gap: 12px;
    font-size: 19px;
    line-height: 29px;
  }
  .contact-list svg { width: 16px; height: 16px; flex: none; }
</style>
</head>
<body>

  <section class="card card--back" aria-label="Card back">
    <div class="wordmark">The Brightwater Joint Centre</div>
    <div class="web-address">www.brightwaterjoint.com</div>
  </section>

  <section class="card card--front" aria-label="Card front">
    <div class="card-band" role="img" aria-label="Sky-blue decorative wave band with navy accents"></div>

    <div class="wordmark">The Brightwater Joint Centre</div>

    <div class="holder">
      <p><span class="holder-name">Maren Holloway,</span> <span class="holder-title">Title</span></p>
      <p class="holder-address">Street Name, City Name<br>Zipcode - 012345</p>
      <ul class="contact-list">
        <li>
          <svg viewBox="0 0 16 16"><circle cx="8" cy="8" r="7.5" fill="var(--sky)"/><path d="M5.5,4 L7,4 L7.5,6 L6.6,6.8 C7.1,8 8,8.9 9.2,9.4 L10,8.5 L12,9 L12,10.5 C8,11 5,8 5.5,4 Z" fill="var(--paper)"/></svg>
          012-555-0199
        </li>
        <li>
          <svg viewBox="0 0 16 16"><rect x="1" y="3" width="14" height="10" rx="1.5" fill="var(--sky)"/><path d="M1.5,4 L8,9 L14.5,4" fill="none" stroke="var(--paper)" stroke-width="1.3"/></svg>
          info@brightwaterjoint.com
        </li>
        <li>
          <svg viewBox="0 0 16 16"><circle cx="8" cy="8" r="7" fill="none" stroke="var(--sky)" stroke-width="1.3"/><ellipse cx="8" cy="8" rx="3" ry="7" fill="none" stroke="var(--sky)" stroke-width="1.1"/><path d="M1,8 H15 M2.5,4.5 H13.5 M2.5,11.5 H13.5" stroke="var(--sky)" stroke-width="1"/></svg>
          www.brightwaterjoint.com
        </li>
      </ul>
    </div>
  </section>

</body>
</html>
```